Creative, Colorful, Dynamic Infographic for Global Non-Profit

We are a global arts and education non-profit in need of an infographic that illustrates four key skills embedded in our work: Curiosity, Listening, Imagination, Postive Action.
We work primarily with educators, students, and artists who use the power of personal stories to build community and connection and to bridge divides.
Our new brand guidelines, logos, and fonts are here: https://stylevault.example/lumen-circle
I've attached a mock-up of the graphic and the required text. (Note the attached design was created by a staff person, your final design does not need to be the same. The color scheme and text of the final design should match the brand guidelines above.)
The graphic will be used for both web and print media and should include the purple Lumen Circle logo (also attached).
Ideally the final design will delight audiences and spark interest in our work.

```html
<!DOCTYPE html>
<html lang="en">
<head>
<meta charset="UTF-8">
<title>Lumen Circle – Four Key Practices</title>
<link rel="stylesheet" href="https://fonts.googleapis.com/css2?family=Montserrat:wght@500;600;700;800&display=swap">
<style>
  :root {
    --brand-purple: #643399;
    --ink: #1c1c1c;
    --curiosity: #e6c84a;
    --listening: #f19656;
    --imagination: #4db88a;
    --action: #ea4444;
    --tint-action: #fadadd;
    --tint-curiosity: #faf4de;
    --tint-imagination: #dff1e9;
    --tint-listening: #fde8dc;
    --backdrop: #c2c2c2;
    --paper: #ffffff;
  }
  html, body {
    margin: 0;
    width: 1200px;
    height: 1200px;
    overflow: hidden;
    background: var(--backdrop);
  }
  .poster {
    position: absolute;
    left: 0;
    top: 175px;
    width: 1200px;
    height: 849px;
    display: block;
    background: var(--paper);
    font-family: "Montserrat", sans-serif;
  }
  .brand-name { fill: var(--brand-purple); font-weight: 600; font-size: 46px; }
  .title-top { fill: var(--brand-purple); font-weight: 700; font-size: 68px; }
  .title-bottom { fill: var(--ink); font-weight: 800; font-size: 68px; }
  .practice-heading { font-weight: 700; font-size: 36px; letter-spacing: 1px; }
  .practice-text, .link-text { fill: var(--ink); font-weight: 500; font-size: 22px; letter-spacing: 0.8px; }
  .web-address { fill: var(--brand-purple); font-weight: 700; font-size: 50px; }
  .hub-name { fill: #ffffff; font-weight: 700; font-size: 30px; }
  .side-line { fill: none; stroke-width: 5; }
  .end-dot { fill: var(--paper); stroke-width: 4; }
</style>
</head>
<body>
<svg class="poster" viewBox="0 0 1732 1225" xmlns="http://www.w3.org/2000/svg" aria-label="Four key practices embedded in our work">
  <defs>
    <filter id="soft-shadow" x="-20%" y="-20%" width="140%" height="140%">
      <feDropShadow dx="3" dy="4" stdDeviation="4" flood-color="#000" flood-opacity="0.25"/>
    </filter>
  </defs>

  <!-- Header -->
  <g class="header">
    <circle cx="171" cy="129" r="68" fill="var(--brand-purple)"/>
    <text class="brand-name" x="266" y="145" textLength="390" lengthAdjust="spacingAndGlyphs">LUMEN CIRCLE</text>
    <line x1="690" y1="65" x2="690" y2="182" stroke="var(--ink)" stroke-width="3"/>
    <text class="title-top" x="730" y="112" textLength="760" lengthAdjust="spacingAndGlyphs">FOUR KEY PRACTICES</text>
    <text class="title-bottom" x="730" y="182" textLength="895" lengthAdjust="spacingAndGlyphs">EMBEDDED IN OUR WORK</text>
  </g>

  <!-- Side brackets -->
  <g class="brackets">
    <path class="side-line" stroke="var(--curiosity)" d="M297,266 Q190,430 178,624 H65"/>
    <circle class="end-dot" stroke="var(--curiosity)" cx="305" cy="255" r="12"/>
    <path class="side-line" stroke="var(--listening)" d="M65,709 H178 Q190,905 297,1049"/>
    <circle class="end-dot" stroke="var(--listening)" cx="305" cy="1061" r="12"/>
    <path class="side-line" stroke="var(--action)" d="M1436,266 Q1545,430 1556,624 H1667"/>
    <circle class="end-dot" stroke="var(--action)" cx="1428" cy="255" r="12"/>
    <path class="side-line" stroke="var(--imagination)" d="M1667,709 H1556 Q1545,905 1436,1049"/>
    <circle class="end-dot" stroke="var(--imagination)" cx="1428" cy="1061" r="12"/>
  </g>

  <!-- Link boxes -->
  <g class="link-boxes">
    <rect x="638" y="229" width="455" height="77" fill="var(--tint-action)"/>
    <text class="link-text" x="865" y="262" text-anchor="middle">Your positive actions inspires</text>
    <text class="link-text" x="865" y="290" text-anchor="middle">curiosity about what possible.</text>

    <rect x="217" y="618" width="367" height="77" fill="var(--tint-curiosity)"/>
    <text class="link-text" x="557" y="650" text-anchor="end">Your curiosity motivates</text>
    <text class="link-text" x="557" y="679" text-anchor="end">you to listen.</text>

    <rect x="1135" y="618" width="367" height="77" fill="var(--tint-imagination)"/>
    <text class="link-text" x="1162" y="650">Your imagination sparks</text>
    <text class="link-text" x="1162" y="679">positive action.</text>

    <rect x="638" y="1001" width="455" height="77" fill="var(--tint-listening)"/>
    <text class="link-text" x="865" y="1034" text-anchor="middle">Your listening lets you take</text>
    <text class="link-text" x="865" y="1062" text-anchor="middle">in new information.</text>
  </g>

  <!-- Practices -->
  <g class="practices">
    <text class="practice-heading" fill="var(--curiosity)" x="585" y="402" text-anchor="end">CURIOSITY</text>
    <text class="practice-text" x="584" y="438" text-anchor="end">Learn from another’s</text>
    <text class="practice-text" x="584" y="467" text-anchor="end">knowledge and experience.</text>

    <text class="practice-heading" fill="var(--action)" x="1130" y="402">POSITIVE ACTION</text>
    <text class="practice-text" x="1133" y="438">Show your words and</text>
    <text class="practice-text" x="1133" y="467">actions matter.</text>

    <text class="practice-heading" fill="var(--listening)" x="585" y="860" text-anchor="end">LISTENING</text>
    <text class="practice-text" x="584" y="894" text-anchor="end">Seek to understand</text>
    <text class="practice-text" x="584" y="923" text-anchor="end">before speaking.</text>

    <text class="practice-heading" fill="var(--imagination)" x="1130" y="860">IMAGINATION</text>
    <text class="practice-text" x="1133" y="894">Consider possibilities</text>
    <text class="practice-text" x="1133" y="923">beyond what you know.</text>
  </g>

  <!-- Cycle -->
  <g class="cycle" transform="translate(862,652)">
    <line x1="0" y1="-310" x2="0" y2="-230" stroke="#999" stroke-width="2"/>
    <line x1="0" y1="230" x2="0" y2="320" stroke="#999" stroke-width="2"/>
    <g stroke="#ffffff" stroke-width="2">
      <path fill="var(--action)" transform="rotate(90)" d="M0,-240 A240,240 0 0,0 -236.4,-41.7 L-258,-45.5 L-183.2,66.7 L-126.1,-22.2 L-147.7,-26 A150,150 0 0,1 0,-150 Z"/>
      <path fill="var(--imagination)" transform="rotate(180)" d="M0,-240 A240,240 0 0,0 -236.4,-41.7 L-258,-45.5 L-183.2,66.7 L-126.1,-22.2 L-147.7,-26 A150,150 0 0,1 0,-150 Z"/>
      <path fill="var(--listening)" transform="rotate(-90)" d="M0,-240 A240,240 0 0,0 -236.4,-41.7 L-258,-45.5 L-183.2,66.7 L-126.1,-22.2 L-147.7,-26 A150,150 0 0,1 0,-150 Z"/>
      <path fill="var(--curiosity)" d="M0,-240 A240,240 0 0,0 -236.4,-41.7 L-258,-45.5 L-183.2,66.7 L-126.1,-22.2 L-147.7,-26 A150,150 0 0,1 0,-150 Z"/>
    </g>
    <circle r="150" fill="var(--paper)" filter="url(#soft-shadow)"/>
    <circle r="96" fill="var(--brand-purple)" filter="url(#soft-shadow)"/>
    <text class="hub-name" x="0" y="-4" text-anchor="middle">Lumen</text>
    <text class="hub-name" x="0" y="30" text-anchor="middle">Circle</text>
  </g>

  <!-- Footer -->
  <text class="web-address" x="866" y="1160" text-anchor="middle">www.lumencircle.example</text>
</svg>
</body>
</html>
```